Quarrybend Marble & Tile Needs a Business Card

Attached you will find your logo, my photo and design guidelines for a new business card. The final design will need two separate files to create an embossed card. The cards will be printed by www.plinkprint.com (Instructions below)
Format is the Plink SQUARE card
Quarrybend Marble And Tile is a brick and mortar, retail stone and tile shop.
One the front:
Quarrybend Marble And Tile
Dorian Fesslock
Owner
24807 Hollis Verdant Blvd
Suite P & R
Charlotte, NC 28193
Cell: 704-583-7142
Web: www.QuarrybendMarbleAndTile.com
(Make each word of the domain a different or alternating color)
On the back;
Something that shows beautiful colorful tile
Follow the design guide closely please. For more information see this page that describes creating the spot gloss file: https://www.plinkprint.com/us/business-cards/design-guidelines-spot-gloss
The logo is what we would like to have raised spot glossed.
Format is the Plink SQUARE card. See attahced guidlines.

```html
<!DOCTYPE html>
<html lang="en">
<head>
<meta charset="utf-8">
<title>Quarrybend Marble &amp; Tile — Square Business Card</title>
<link href="https://fonts.googleapis.com/css2?family=Cinzel:wght@500&family=Cormorant+Garamond:wght@600&family=Montserrat:wght@400;500&display=swap" rel="stylesheet">
<style>
  :root {
    --stage: #6f7073;
    --navy: #2c3742;
    --navy-raised: #3a4755;
    --ink: #1f2d3a;
    --paper: #fdfdfd;
    --rust: #b5471f;
    --gold: #d19a2f;
    --stone-grey: #7d7f7a;
    --tan: #c08a3a;
    --photo-tone: #3b4652;
  }
  * { margin: 0; padding: 0; box-sizing: border-box; }
  html, body {
    width: 1200px; height: 900px; overflow: hidden;
    background: var(--stage);
  }
  .canvas { position: relative; width: 1200px; height: 900px; }

  .card {
    position: absolute; top: 219px;
    width: 461px; height: 462px;
  }

  /* Back side */
  .card-back { left: 112px; background: var(--navy); }
  .back-mark {
    position: absolute; left: 47px; top: 176px;
    width: 108px; height: 108px;
    background: var(--navy-raised);
  }
  .back-name {
    position: absolute; left: 175px; top: 190px; width: 250px;
    font-family: "Cinzel", serif; font-weight: 500;
    color: var(--navy-raised);
  }
  .back-name .line-1 { display: block; font-size: 31px; letter-spacing: 3px; line-height: 40px; }
  .back-name .line-2 { display: block; font-size: 17px; letter-spacing: 7px; line-height: 34px; }

  /* Front side */
  .card-front { left: 627px; background: var(--paper); }
  .brand-mark {
    position: absolute; left: 39px; top: 42px;
    width: 104px; height: 104px;
    background: var(--ink);
  }
  .brand-name {
    position: absolute; left: 170px; top: 62px; width: 270px;
    font-family: "Cinzel", serif; font-weight: 500;
    color: var(--ink);
  }
  .brand-name .line-1 { display: block; font-size: 31px; letter-spacing: 3px; line-height: 40px; }
  .brand-name .line-2 { display: block; font-size: 17px; letter-spacing: 7px; line-height: 32px; }

  .person-name {
    position: absolute; left: 33px; top: 202px;
    font-family: "Cormorant Garamond", serif; font-weight: 600;
    font-size: 27px; color: var(--ink); letter-spacing: 0.5px;
  }
  .person-title {
    position: absolute; left: 32px; top: 230px;
    font-family: "Montserrat", sans-serif; font-size: 14px;
    color: var(--rust); letter-spacing: 0.5px;
  }
  .divider { position: absolute; left: 33px; top: 257px; }

  .portrait {
    position: absolute; left: 340px; top: 206px;
    width: 89px; height: 90px;
    background: linear-gradient(160deg, #55606b, var(--photo-tone));
    border: 2px solid var(--tan);
  }

  .address {
    position: absolute; left: 33px; top: 276px;
    font-family: "Montserrat", sans-serif; font-size: 14px;
    line-height: 24.5px; color: var(--ink); font-style: normal;
  }
  .contacts {
    position: absolute; left: 32px; top: 361px; list-style: none;
    font-family: "Montserrat", sans-serif; font-size: 14.5px; color: var(--ink);
  }
  .contacts li { display: flex; align-items: center; height: 25px; letter-spacing: 0.6px; }
  .contacts li.phone { letter-spacing: 2.4px; }
  .contacts svg { width: 14px; height: 14px; margin-right: 6px; flex: none; }
  .d-1 { color: var(--rust); }
  .d-2 { color: var(--gold); }
  .d-3 { color: var(--stone-grey); }
  .d-4 { color: var(--tan); }
</style>
</head>
<body>
<main class="canvas">

  <section class="card card-back" aria-label="Card back">
    <div class="back-mark"></div>
    <div class="back-name">
      <span class="line-1">QUARRYBEND</span>
      <span class="line-2">MARBLE &amp; TILE</span>
    </div>
  </section>

  <section class="card card-front" aria-label="Card front">
    <div class="brand-mark"></div>
    <div class="brand-name">
      <span class="line-1">QUARRYBEND</span>
      <span class="line-2">MARBLE &amp; TILE</span>
    </div>

    <h1 class="person-name">Dorian Fesslock</h1>
    <p class="person-title">Owner</p>

    <svg class="divider" width="306" height="4" viewBox="0 0 306 4">
      <line x1="0" y1="2" x2="306" y2="2" stroke="var(--ink)" stroke-width="2" stroke-dasharray="18 5"/>
    </svg>

    <div class="portrait" role="img" aria-label="Portrait photo of Dorian Fesslock"></div>

    <address class="address">
      24807 Hollis Verdant Blvd<br>
      Suite P &amp; R<br>
      Charlotte, NC 28193
    </address>

    <ul class="contacts">
      <li class="phone">
        <svg viewBox="0 0 24 24"><path fill="var(--rust)" d="M6.6 10.8a15.1 15.1 0 0 0 6.6 6.6l2.2-2.2c.3-.3.7-.4 1-.2 1.1.4 2.3.6 3.6.6.6 0 1 .4 1 1V20c0 .6-.4 1-1 1A17 17 0 0 1 3 4c0-.6.4-1 1-1h3.5c.6 0 1 .4 1 1 0 1.3.2 2.5.6 3.6.1.3 0 .7-.2 1z"/></svg>
        704-583-7142
      </li>
      <li>
        <svg viewBox="0 0 24 24"><rect x="2" y="5" width="20" height="14" fill="var(--rust)"/><path d="M2 5l10 8 10-8M2 19l7-7M22 19l-7-7" stroke="#fff" stroke-width="1.6" fill="none"/></svg>
        <span>info@<span class="d-1">Quarrybend</span><span class="d-2">Marble</span><span class="d-3">And</span><span class="d-4">Tile</span>.com</span>
      </li>
      <li>
        <svg viewBox="0 0 24 24"><g fill="none" stroke="var(--rust)" stroke-width="2"><circle cx="12" cy="12" r="9"/><ellipse cx="12" cy="12" rx="4" ry="9"/><path d="M3 12h18M5 7h14M5 17h14"/></g></svg>
        <span>www.<span class="d-1">Quarrybend</span><span class="d-2">Marble</span><span class="d-3">And</span><span class="d-4">Tile</span>.com</span>
      </li>
    </ul>
  </section>

</main>
</body>
</html>
```